My Web Development Portfolio site

I'm a web developer and I need a web design that can showcase my web development portfolio. I like most of the websites from this link: http://www.lumivexa.com/portfolios/examples-503917. My ideal design should be modern, clean and fun. I will let the designer decided the color theme for the website.

Target Market(s)

Potential Employers.

Number of Pages Required

1 page

Requirements
Must have
• - Menu bar that includes at least: About Me, Blog, Contact, Project/Work
• - Excellent color theme
• - Use the logo I provided (see attachment)
Nice to have
• - Some animation
• - Fun yet modern design

```html
<!DOCTYPE html>
<html lang="en">
<head>
<meta charset="utf-8">
<title>Bytecrest — Web Design &amp; Development</title>
<link rel="stylesheet" href="https://fonts.googleapis.com/css2?family=Open+Sans:wght@300;400;600;700&display=swap">
<style>
:root{
  --orange:#e8711c;
  --brown:#6e300d;
  --dark:#141414;
  --darker:#0c0c0c;
  --grey-text:#6a6a6a;
  --light-grey:#f2f2f2;
  --white:#ffffff;
}
*{margin:0;padding:0;box-sizing:border-box}
html,body{width:1200px;height:3200px;overflow:hidden}
body{font-family:"Open Sans",Arial,sans-serif;color:var(--grey-text);background:var(--white);position:relative}
.section{position:absolute;left:0;width:1200px}
.btn{display:inline-block;background:var(--brown);color:var(--white);font-size:12px;font-weight:600;padding:6px 14px;border-radius:3px}
.section-title{text-align:center;font-size:30px;font-weight:400;color:#333}
.section-title span{color:var(--orange)}
.title-mark{display:block;margin:6px auto 0;width:14px;height:14px;border:2px solid var(--orange);border-radius:50%}

/* top bar */
.topbar{top:0;height:36px;background:var(--darker);color:#ccc;font-size:12px}
.topbar .phone{position:absolute;left:40px;top:10px}
.topbar .mail{position:absolute;right:40px;top:10px}
.topbar i{display:inline-block;width:10px;height:10px;background:var(--orange);border-radius:2px;margin-right:6px;vertical-align:-1px}

/* nav */
.nav{top:36px;height:96px;background:var(--white)}
.brand{position:absolute;left:40px;top:24px;display:flex;align-items:center;gap:10px}
.brand-dot{width:40px;height:40px;border-radius:50%;background:var(--orange)}
.brand-name{font-size:34px;font-weight:400;color:#555;letter-spacing:.5px}
.menu{position:absolute;right:40px;top:34px;display:flex;gap:4px;list-style:none}
.menu li{font-size:14px;color:#555;padding:6px 16px;border-right:1px solid #ddd}
.menu li:last-child{border-right:none}
.menu li.active{background:var(--dark);color:var(--white);border-radius:2px}

/* hero */
.hero{top:132px;height:540px}
.hero-photo{position:absolute;inset:0;background:linear-gradient(135deg,#e8e3dc 0%,#cfc6bb 30%,#8a5a34 55%,#5a3318 80%,#3a2010 100%)}
.hero-screen{position:absolute;left:620px;top:20px;width:460px;height:300px;background:linear-gradient(160deg,#1c2630,#0d1318);transform:rotate(-6deg);border-radius:6px}
.hero-copy{position:absolute;left:0;width:1200px;top:255px;text-align:center}
.hero-copy h1{font-size:40px;font-weight:300;color:var(--white)}
.hero-copy p{font-size:22px;color:var(--orange);margin-top:2px}
.hero-dots{position:absolute;left:570px;top:430px;display:flex;gap:8px}
.hero-dots span{width:9px;height:9px;border-radius:50%;background:#bbb}
.hero-dots span:first-child{background:var(--white)}
.hero-curve{position:absolute;left:0;bottom:0}

/* welcome */
.welcome{top:680px;height:280px}
.welcome h2{position:absolute;left:100px;top:0;font-size:30px;font-weight:400;color:#333}
.welcome h2 span{color:var(--orange)}
.welcome p{position:absolute;left:100px;top:56px;width:560px;font-size:13px;line-height:20px}
.welcome .btn{position:absolute;left:100px;top:210px}
.welcome-photo{position:absolute;left:780px;top:10px;width:320px;height:220px;background:linear-gradient(180deg,#f4f4f4,#dedede);}
.welcome-photo .monitor{position:absolute;left:40px;top:20px;width:240px;height:150px;background:#1e1e1e;border-radius:4px}
.welcome-photo .monitor-name{position:absolute;left:0;right:0;top:60px;text-align:center;color:#ddd;font-size:20px}

/* services */
.services{top:980px;height:480px}
.services svg.band{position:absolute;left:0;top:0}
.services .section-title{position:absolute;top:70px;width:1200px;color:var(--white)}
.service{position:absolute;top:170px;width:300px;text-align:center;color:#cfcfcf}
.service .icon{width:78px;height:78px;margin:0 auto;border-radius:50%;background:var(--orange);display:flex;align-items:center;justify-content:center}
.service h3{font-size:19px;font-weight:400;color:var(--white);margin-top:16px}
.service p{font-size:12px;line-height:18px;margin:8px 20px 0}
.service .btn{margin-top:16px}

/* projects */
.projects{top:1470px;height:760px}
.projects .section-title{position:absolute;top:30px;width:1200px}
.projects .title-mark{position:absolute;left:593px;top:80px}
.card{position:absolute;width:320px;height:232px;background:var(--white);box-shadow:0 1px 4px rgba(0,0,0,.25)}
.card .shot{height:182px}
.card .caption{position:absolute;left:0;bottom:0;width:100%;height:50px;display:flex;align-items:center;padding-left:16px;font-size:15px;color:#444}
.card .arrow{position:absolute;right:0;top:0;width:50px;height:50px;background:var(--brown);display:flex;align-items:center;justify-content:center}
.projects .btn{position:absolute;left:565px;top:695px}

/* blog */
.blog{top:2250px;height:570px}
.blog-photo{position:absolute;inset:0;background:linear-gradient(180deg,#d9d9d9 0%,#9a9a9a 45%,#5c5c5c 100%)}
.blog .section-title{position:absolute;top:40px;width:1200px;color:#f2f2f2}
.blog .title-mark{position:absolute;left:593px;top:88px}
.post{position:absolute;top:120px;width:320px;height:370px;background:var(--white)}
.post .shot{height:180px;position:relative}
.date{position:absolute;left:14px;top:0;width:46px;text-align:center;color:var(--white);font-size:11px}
.date b{display:block;background:var(--dark);padding:2px 0;font-weight:600}
.date span{display:block;background:var(--orange);font-size:18px;padding:3px 0;font-weight:600}
.post h4{font-size:15px;font-weight:400;color:var(--orange);text-align:center;margin-top:16px}
.post p{font-size:12px;line-height:18px;text-align:center;margin:10px 22px 0}
.post .btn{position:absolute;left:50%;transform:translateX(-50%);bottom:20px}

/* newsletter */
.newsletter{top:2820px;height:100px;background:#1b120c}
.newsletter .env{position:absolute;left:100px;top:28px;width:44px;height:44px;border-radius:50%;background:var(--orange);display:flex;align-items:center;justify-content:center}
.newsletter h3{position:absolute;left:158px;top:33px;font-size:24px;font-weight:600;color:var(--white)}
.newsletter .sep{position:absolute;left:392px;top:30px;width:1px;height:40px;background:#555}
.newsletter p{position:absolute;left:410px;top:34px;width:190px;font-size:12px;line-height:16px;color:#ccc}
.newsletter .field{position:absolute;left:760px;top:36px;width:230px;height:28px;background:var(--white);font-size:12px;color:#999;padding:6px 10px}
.newsletter .subscribe{position:absolute;left:1000px;top:36px;height:28px;width:100px;background:#2a2a2a;border:1px solid #555;color:var(--white);font-size:12px;text-align:center;line-height:26px}

/* footer */
.footer{top:2920px;height:240px;background:var(--darker);color:#aaa}
.footer .brand{left:100px;top:80px}
.footer .brand-name{color:#ddd}
.fcol{position:absolute;top:36px;font-size:12px;line-height:22px}
.fcol h5{font-size:14px;font-weight:400;color:var(--white);margin-bottom:8px}
.fcol ul{list-style:none}
.fcol li::before{content:"";display:inline-block;width:4px;height:4px;background:var(--orange);margin-right:8px;vertical-align:2px}
.fcol.social li::before{width:14px;height:14px;border-radius:2px;vertical-align:-3px}
.fsep{position:absolute;top:36px;width:1px;height:170px;background:#333}
.copyright{top:3160px;height:40px;background:#000;color:#888;font-size:11px;text-align:center;line-height:40px}
</style>
</head>
<body>

<header class="section topbar">
  <div class="phone"><i></i>555 014 229</div>
  <div class="mail"><i></i>hello@bytecrest.dev</div>
</header>

<nav class="section nav">
  <div class="brand"><div class="brand-dot"></div><div class="brand-name">bytecrest</div></div>
  <ul class="menu">
    <li class="active">Home</li>
    <li>About Me</li>
    <li>Project/Work</li>
    <li>Blog</li>
    <li>Contact</li>
  </ul>
</nav>

<section class="section hero">
  <div class="hero-photo" role="img" aria-label="Designer's desk with wireframe sketches, a tablet showing code and a cup of tea on a wooden table"></div>
  <div class="hero-screen"></div>
  <div class="hero-copy">
    <h1>Web Design &amp; Development</h1>
    <p>Custom solutions for companies and individuals</p>
  </div>
  <div class="hero-dots"><span></span><span></span><span></span><span></span></div>
  <svg class="hero-curve" width="1200" height="60" viewBox="0 0 1200 60"><path d="M0 60 Q600 -10 1200 60 Z" fill="#ffffff"/></svg>
</section>

<section class="section welcome">
  <h2>Welcome to <span>Bytecrest</span></h2>
  <p>Lorem ipsum dolor sit amet, consectetuer adipiscing elit, sed diam nonummy nibh euismod tincidunt ut laoreet dolore magna aliquam erat volutpat. Ut wisi enim ad minim veniam, quis nostrud exerci tation ullamcorper suscipit lobortis nisl ut aliquip ex ea commodo consequat. Duis autem vel eum iriure dolor in hendrerit in vulputate velit esse molestie consequat, vel illum dolore eu feugiat nulla facilisis at vero eros et.</p>
  <span class="btn">Read More</span>
  <div class="welcome-photo" role="img" aria-label="Desktop monitor on a white desk showing the studio name">
    <div class="monitor"><div class="monitor-name">bytecrest</div></div>
  </div>
</section>

<section class="section services">
  <svg class="band" width="1200" height="480" viewBox="0 0 1200 480"><path d="M0 40 Q600 -30 1200 40 L1200 440 Q600 510 0 440 Z" fill="#141414"/></svg>
  <h2 class="section-title">Our <span>Services</span></h2>
  <div class="service" style="left:150px">
    <div class="icon"><svg width="44" height="40" viewBox="0 0 44 40" fill="#fff"><circle cx="22" cy="11" r="7"/><path d="M10 36c0-8 5-13 12-13s12 5 12 13z"/><circle cx="8" cy="15" r="5"/><path d="M0 34c0-6 3-9 8-9 2 0 3 .5 4 1-2 2-3 5-3 8z"/><circle cx="36" cy="15" r="5"/><path d="M44 34c0-6-3-9-8-9-2 0-3 .5-4 1 2 2 3 5 3 8z"/></svg></div>
    <h3>Potential Employers</h3>
    <p>Lorem ipsum dolor sit amet, consectetuer adipiscing elit, sed diam nonummy nibh euismod tincidunt ut laoreet.</p>
    <span class="btn">Read More</span>
  </div>
  <div class="service" style="left:450px">
    <div class="icon"><svg width="44" height="40" viewBox="0 0 44 40" fill="none" stroke="#fff" stroke-width="3"><rect x="3" y="3" width="38" height="26" rx="2"/><path d="M16 37h12M22 29v8"/><path d="M14 22l12-12 4 4-12 12h-4z" fill="#fff" stroke="none"/></svg></div>
    <h3>Websites Design</h3>
    <p>Lorem ipsum dolor sit amet, consectetuer adipiscing elit, sed diam nonummy nibh euismod tincidunt ut laoreet.</p>
    <span class="btn">Read More</span>
  </div>
  <div class="service" style="left:750px">
    <div class="icon"><svg width="44" height="40" viewBox="0 0 44 40" fill="none" stroke="#fff" stroke-width="3"><rect x="3" y="3" width="38" height="26" rx="2"/><path d="M16 37h12M22 29v8M16 12l-5 4 5 4M28 12l5 4-5 4"/></svg></div>
    <h3>Websites Development</h3>
    <p>Lorem ipsum dolor sit amet, consectetuer adipiscing elit, sed diam nonummy nibh euismod tincidunt ut laoreet.</p>
    <span class="btn">Read More</span>
  </div>
</section>

<section class="section projects">
  <h2 class="section-title">Our <span>Project / Work</span></h2>
  <span class="title-mark"></span>
  <div class="card" style="left:100px;top:140px"><div class="shot" role="img" aria-label="Screenshot of a corporate website in blue tones" style="background:linear-gradient(160deg,#2a3a4a,#3aa0c8 60%,#e8eef2)"></div><div class="caption">Lorem ipsum dolor.<span class="arrow"><svg width="12" height="14" viewBox="0 0 12 14"><path d="M2 1l8 6-8 6z" fill="#fff"/></svg></span></div></div>
  <div class="card" style="left:440px;top:140px"><div class="shot" role="img" aria-label="Screenshot of a light website with icon tiles" style="background:linear-gradient(160deg,#f4f7fa,#cfe3ef 60%,#6fb6d8)"></div><div class="caption">Consectetuer adipiscing.<span class="arrow"><svg width="12" height="14" viewBox="0 0 12 14"><path d="M2 1l8 6-8 6z" fill="#fff"/></svg></span></div></div>
  <div class="card" style="left:780px;top:140px"><div class="shot" role="img" aria-label="Screenshot of a dark dashboard website" style="background:linear-gradient(160deg,#2b3038,#4a5460 60%,#8a96a4)"></div><div class="caption">Sed diam nonummy.<span class="arrow"><svg width="12" height="14" viewBox="0 0 12 14"><path d="M2 1l8 6-8 6z" fill="#fff"/></svg></span></div></div>
  <div class="card" style="left:100px;top:420px"><div class="shot" role="img" aria-label="Screenshot of a green nature-themed website" style="background:linear-gradient(160deg,#1c2a1e,#3e5a3a 60%,#8aa07a)"></div><div class="caption">Lorem ipsum dolor.<span class="arrow"><svg width="12" height="14" viewBox="0 0 12 14"><path d="M2 1l8 6-8 6z" fill="#fff"/></svg></span></div></div>
  <div class="card" style="left:440px;top:420px"><div class="shot" role="img" aria-label="Screenshot of a purple agency website" style="background:linear-gradient(160deg,#3a2a5a,#6a4a9a 60%,#e6e0ee)"></div><div class="caption">Consectetuer adipiscing.<span class="arrow"><svg width="12" height="14" viewBox="0 0 12 14"><path d="M2 1l8 6-8 6z" fill="#fff"/></svg></span></div></div>
  <div class="card" style="left:780px;top:420px"><div class="shot" role="img" aria-label="Screenshot of a construction company website in navy tones" style="background:linear-gradient(160deg,#10203a,#24406a 60%,#6a86aa)"></div><div class="caption">Sed diam nonummy.<span class="arrow"><svg width="12" height="14" viewBox="0 0 12 14"><path d="M2 1l8 6-8 6z" fill="#fff"/></svg></span></div></div>
  <span class="btn">View All</span>
</section>

<section class="section blog">
  <div class="blog-photo" role="img" aria-label="Greyscale photo of a team working together in an office"></div>
  <h2 class="section-title">Latest <span>Blog</span></h2>
  <span class="title-mark"></span>
  <article class="post" style="left:100px">
    <div class="shot" role="img" aria-label="Business team in a meeting" style="background:linear-gradient(160deg,#cfd8e0,#6a7a8a)"><div class="date"><b>Apr</b><span>21</span></div></div>
    <h4>Lorem ipsum dolor sit amet.</h4>
    <p>Lorem ipsum dolor sit amet, consectetuer adipiscing elit, sed diam nonummy nibh euismod tincidunt ut laoreet dolore magna.</p>
    <span class="btn">Read More</span>
  </article>
  <article class="post" style="left:440px">
    <div class="shot" role="img" aria-label="Colleagues discussing at a bright office table" style="background:linear-gradient(160deg,#eef0f2,#a8b0b8)"><div class="date"><b>Apr</b><span>21</span></div></div>
    <h4>Consectetuer adipiscing elit.</h4>
    <p>Lorem ipsum dolor sit amet, consectetuer adipiscing elit, sed diam nonummy nibh euismod tincidunt ut laoreet dolore magna.</p>
    <span class="btn">Read More</span>
  </article>
  <article class="post" style="left:780px">
    <div class="shot" role="img" aria-label="Two professionals shaking hands in an office" style="background:linear-gradient(160deg,#e4e8ea,#7a8a80)"><div class="date"><b>Apr</b><span>21</span></div></div>
    <h4>Sed diam nonummy nibh.</h4>
    <p>Lorem ipsum dolor sit amet, consectetuer adipiscing elit, sed diam nonummy nibh euismod tincidunt ut laoreet dolore magna.</p>
    <span class="btn">Read More</span>
  </article>
</section>

<section class="section newsletter">
  <div class="env"><svg width="22" height="16" viewBox="0 0 22 16" fill="none" stroke="#fff" stroke-width="2"><rect x="1" y="1" width="20" height="14"/><path d="M1 1l10 8 10-8"/></svg></div>
  <h3>Newsletter Signup</h3>
  <div class="sep"></div>
  <p>Sign up for free email updates from our studio today.</p>
  <div class="field">Enter Your Email</div>
  <div class="subscribe">Subscribe</div>
</section>

<footer class="section footer">
  <div class="brand"><div class="brand-dot"></div><div class="brand-name">bytecrest</div></div>
  <div class="fsep" style="left:390px"></div>
  <div class="fcol" style="left:420px">
    <h5>Quick Links</h5>
    <ul><li>Home</li><li>About Me</li><li>Project/Work</li><li>Blog</li><li>Contact</li></ul>
  </div>
  <div class="fsep" style="left:620px"></div>
  <div class="fcol" style="left:650px">
    <h5>Contact Us</h5>
    <p>Bytecrest<br>Lorem ipsum dolor sit amet,<br>consectetuer adipiscing 042</p>
    <p style="margin-top:6px">555 014 229<br>hello@bytecrest.dev</p>
  </div>
  <div class="fsep" style="left:920px"></div>
  <div class="fcol social" style="left:950px">
    <h5>Social Connect</h5>
    <ul><li>Friends Page</li><li>Short Posts</li><li>Circles</li><li>Career Profile</li></ul>
  </div>
</footer>

<div class="section copyright">Copyright 2024 · Bytecrest · All Rights Reserved</div>

</body>
</html>
```